Awesome photographers card for an awesome new business

Double sided business card Black background and silver logo in middle on one side. Details on otherside. please keep it simple

Industry/Entity Type

Photographer

Contact Information for Business Card

Gerald Fenwick
0452817360
GeraldFenwickPhotography47@mailbox.test
www.GeraldFenwickPhotography.test.au
Instagram _Gerald_fenwick

Requirements
Must have
• My logo in Silver
• please use instagram logo instead of "Instagram"

```html
<!DOCTYPE html>
<html lang="en">
<head>
<meta charset="utf-8">
<title>Gerald Fenwick Photography – Business Card</title>
<link rel="stylesheet" href="https://fonts.googleapis.com/css2?family=Mulish:wght@400;700;800&display=swap">
<style>
  :root {
    --backdrop: #e9e6e1;
    --card-black: #1b1c1e;
    --card-white: #f7f7f7;
    --silver: #c9cbce;
    --ink: #1a1a1a;
    --ink-soft: #4a4a4a;
    --ghost: #e6e6e6;
  }
  * { margin: 0; padding: 0; box-sizing: border-box; }
  html, body { width: 1200px; height: 960px; overflow: hidden; }
  body {
    background: var(--backdrop);
    font-family: "Mulish", "Century Gothic", sans-serif;
    position: relative;
  }
  .card {
    position: absolute;
    left: 320px;
    width: 600px;
    border-radius: 22px;
    overflow: hidden;
  }
  .card--front {
    top: 100px;
    height: 355px;
    background: var(--card-black);
    display: flex;
    align-items: center;
    justify-content: center;
  }
  .brand-mark {
    width: 180px;
    height: 180px;
    border: 3px solid var(--silver);
    border-radius: 50%;
    display: flex;
    align-items: center;
    justify-content: center;
    text-align: center;
    color: var(--silver);
    font-weight: 700;
    font-size: 14px;
    letter-spacing: 2.5px;
    line-height: 1.6;
    text-transform: uppercase;
  }
  .card--back {
    top: 493px;
    height: 342px;
    background: var(--card-white);
  }
  .ghost-name {
    position: absolute;
    left: 0;
    right: 0;
    top: 52px;
    text-align: center;
    font-size: 72px;
    font-weight: 700;
    color: var(--ghost);
    line-height: 1;
    white-space: nowrap;
  }
  .details {
    position: absolute;
    right: 36px;
    top: 188px;
    text-align: right;
  }
  .details__name {
    font-size: 21px;
    font-weight: 800;
    color: var(--ink);
    letter-spacing: 0.3px;
    margin-bottom: 18px;
    text-transform: uppercase;
  }
  .details__list { list-style: none; }
  .details__item {
    display: flex;
    justify-content: flex-end;
    align-items: center;
    gap: 12px;
    font-size: 14px;
    color: var(--ink-soft);
    height: 19.5px;
  }
  .details__icon { width: 12px; height: 12px; flex: none; fill: var(--ink); }
</style>
</head>
<body>
  <section class="card card--front">
    <div class="brand-mark">Gerald<br>Fenwick<br>Photography</div>
  </section>

  <section class="card card--back">
    <div class="ghost-name" aria-hidden="true">Gerald Fenwick</div>
    <div class="details">
      <h1 class="details__name">Gerald Fenwick</h1>
      <ul class="details__list">
        <li class="details__item">0452817360
          <svg class="details__icon" viewBox="0 0 12 12"><path d="M2.5 0.5l2 2.5-1.2 1.4c.8 1.6 2 2.8 3.6 3.6L8.3 6.8l2.7 2-1 2.5C5 11 1 7 0.7 2z"/></svg>
        </li>
        <li class="details__item">GeraldFenwickPhotography47@mailbox.test
          <svg class="details__icon" viewBox="0 0 12 12"><path d="M0 2h12v8H0z M0 2.5l6 4 6-4" stroke="#f7f7f7" stroke-width="1"/></svg>
        </li>
        <li class="details__item">www.GeraldFenwickPhotography.test.au
          <svg class="details__icon" viewBox="0 0 12 12"><circle cx="6" cy="6" r="5.5"/><path d="M0.5 6h11M6 0.5c-2.5 3-2.5 8 0 11M6 0.5c2.5 3 2.5 8 0 11" stroke="#f7f7f7" stroke-width="0.9" fill="none"/></svg>
        </li>
        <li class="details__item">Gerald_fenwick
          <svg class="details__icon" viewBox="0 0 12 12"><rect x="0" y="0" width="12" height="12" rx="2"/></svg>
        </li>
      </ul>
    </div>
  </section>
</body>
</html>
```